"Harbor Builders" is a residential building company and needs a new business card design and may re

We would like a redesign based on the existing logo, and would like to see a new font as well. We are bespoke home builders who build sustainable energy efficient homes.

Industry/Entity Type

Construction

Contact Information for Business Card

Business card size 40mm x 90mm

Colors

Designer to choose colors to be used in the design.

```html
<!DOCTYPE html>
<html lang="en">
<head>
<meta charset="utf-8">
<title>Harbor Builders – Business Card</title>
<link rel="stylesheet" href="https://fonts.googleapis.com/css2?family=Source+Sans+3:wght@400;600;700&display=swap">
<style>
  :root {
    --backdrop: #8b8c8e;
    --card-light: #dcdcde;
    --card-dark: #060708;
    --ink: #1f2022;
    --ink-soft: #3a3b3e;
    --accent: #a4c03a;
    --reverse: #e6e6e8;
  }
  * { margin: 0; padding: 0; box-sizing: border-box; }
  html, body {
    width: 1105px; height: 1200px; overflow: hidden;
    background: var(--backdrop);
    font-family: "Source Sans 3", "Myriad Pro", Arial, sans-serif;
  }
  .canvas { position: relative; width: 1105px; height: 1200px; }
  .card {
    position: absolute; left: 182px; width: 747px; height: 425px;
  }
  .card--front { top: 119px; background: var(--card-light); color: var(--ink); }
  .card--back { top: 636px; background: var(--card-dark); }

  .contact { position: absolute; left: 45px; top: 160px; }
  .contact__name { font-size: 27px; font-weight: 700; color: var(--ink); letter-spacing: 0.2px; }
  .contact__address { margin-top: 10px; font-size: 17px; line-height: 22px; color: var(--ink-soft); }
  .contact__company { font-weight: 600; }
  .contact__list { list-style: none; margin-top: 14px; font-size: 17px; line-height: 24px; color: var(--ink-soft); }
  .contact__list li { display: flex; align-items: center; gap: 10px; }
  .contact__list svg { width: 15px; height: 15px; fill: var(--ink); flex: none; }
  .contact__legal { margin-top: 14px; font-size: 15px; color: var(--ink-soft); }
  .contact__legal b { font-weight: 600; }

  .brand {
    position: absolute; inset: 0;
    display: flex; align-items: center; justify-content: center; gap: 26px;
  }
  .brand__square { width: 64px; height: 64px; background: var(--accent); }
  .brand__name { font-size: 56px; font-weight: 600; color: var(--reverse); letter-spacing: 0.5px; }
</style>
</head>
<body>
<main class="canvas">
  <section class="card card--front">
    <div class="contact">
      <h1 class="contact__name">Daniel Moretti</h1>
      <p class="contact__address">
        <span class="contact__company">Harbor Builders Pty Ltd</span><br>
        PO Box 4120 Northgate<br>
        LPO Bayview WA 6000
      </p>
      <ul class="contact__list">
        <li><svg viewBox="0 0 16 16" aria-hidden="true"><path d="M4 0h8a1 1 0 0 1 1 1v14a1 1 0 0 1-1 1H4a1 1 0 0 1-1-1V1a1 1 0 0 1 1-1zm1 2v10h6V2zm3 11a1 1 0 1 0 0 2 1 1 0 0 0 0-2z"/></svg>0400 555 018</li>
        <li><svg viewBox="0 0 16 16" aria-hidden="true"><path d="M1 3h14v1.5L8 9 1 4.5zm0 3.3L8 11l7-4.7V13H1z"/></svg>daniel@harborbuilders.com.au</li>
        <li><svg viewBox="0 0 16 16" aria-hidden="true"><circle cx="8" cy="8" r="7.5"/><path d="M5 4c2 0 3 1 2 3s-3 1-3 3 2 1 2 3M11 3c-1 2 1 3 2 4M10 12c0-2 2-2 3-3" stroke="#dcdcde" stroke-width="1.3" fill="none"/></svg>www.harborbuilders.com.au</li>
      </ul>
      <p class="contact__legal"><b>Registration:</b> 40871 &nbsp;<b>ABN:</b> 12 345 678 901</p>
    </div>
  </section>

  <section class="card card--back">
    <div class="brand">
      <span class="brand__square" aria-hidden="true"></span>
      <span class="brand__name">harbor builders</span>
    </div>
  </section>
</main>
</body>
</html>
```